Business cards and stationary design

We just completed the design of our new logo and we need to print new business cards and letterhead for our nonprofit. We are looking for a fresh new design that shows off our new logo. On letterhead, we must have a column on the right or left to include our Board of Directors (up to 45 names) (see attachment)

Industry/Entity Type

Non-Profit

Contact Information for Business Card

Standard business card with name, title, Company name, mailing address phone numbers, email address and website. Tagline on back "Opening every door to home"

Font styles to use
Sans Serif

Requirements
Must have
• include pertinent information above
• new logo
• fonts compatible with logo
• should use logo colors only
Nice to have
• tag lines

```html
<!DOCTYPE html>
<html lang="en">
<head>
<meta charset="utf-8">
<title>Harbor Shelter Alliance – Business Card</title>
<link rel="stylesheet" href="https://fonts.googleapis.com/css2?family=Aldrich&family=Arimo:wght@400;700&display=swap">
<style>
  :root {
    --backdrop: #dcdcdc;
    --paper: #f7f7f7;
    --teal: #0a83a6;
    --red: #d81f26;
    --yellow: #f9b71b;
    --white: #ffffff;
    --ink-grey: #4a4a4a;
  }
  html, body {
    margin: 0;
    padding: 0;
    width: 1200px;
    height: 582px;
    overflow: hidden;
    background: var(--backdrop);
  }
  .canvas {
    position: relative;
    width: 1200px;
    height: 582px;
  }
  .card {
    position: absolute;
    background: var(--paper);
    overflow: hidden;
    box-shadow: 1px 2px 3px rgba(0,0,0,0.35);
  }
  .card--front {
    left: 198px;
    top: 59px;
    width: 264px;
    height: 463px;
  }
  .card--back {
    left: 526px;
    top: 158px;
    width: 462px;
    height: 264px;
  }
  .brand-name {
    position: absolute;
    left: 0;
    width: 100%;
    text-align: center;
    font-family: "Aldrich", sans-serif;
    font-weight: 400;
    color: var(--teal);
    letter-spacing: 1px;
    margin: 0;
    white-space: nowrap;
  }
  .card--front .brand-name {
    top: 112px;
    font-size: 13px;
  }
  .card--back .brand-name {
    top: 112px;
    font-size: 22px;
  }
  .card-bands {
    position: absolute;
    left: 0;
    top: 0;
    width: 264px;
    height: 463px;
  }
  .contact {
    position: absolute;
    left: 53px;
    top: 280px;
    color: var(--white);
    font-family: "Arimo", sans-serif;
  }
  .contact__name {
    font-family: "Aldrich", sans-serif;
    color: var(--yellow);
    font-size: 17px;
    font-weight: 400;
    letter-spacing: 1.2px;
    margin: 0;
    line-height: 20px;
  }
  .contact__title {
    font-family: "Aldrich", sans-serif;
    font-size: 9.5px;
    letter-spacing: 1px;
    margin: 0 0 14px;
  }
  .contact__address {
    font-style: normal;
    font-size: 11px;
    line-height: 13.5px;
    margin-bottom: 10px;
  }
  .contact__list {
    list-style: none;
    margin: 0;
    padding: 0;
    font-size: 11px;
    line-height: 15px;
  }
  .contact__list li {
    display: flex;
    align-items: center;
    gap: 7px;
  }
  .contact__icon {
    width: 10px;
    height: 10px;
    flex: none;
  }
  .tagline {
    position: absolute;
    left: 0;
    top: 222px;
    width: 100%;
    text-align: center;
    font-family: "Arimo", sans-serif;
    font-weight: 700;
    font-size: 12px;
    letter-spacing: 0.4px;
    color: var(--ink-grey);
    margin: 0;
  }
</style>
</head>
<body>
<main class="canvas">
  <section class="card card--front" aria-label="Business card front">
    <svg class="card-bands" viewBox="0 0 264 463" aria-hidden="true">
      <path d="M0,262 C55,205 190,200 264,268 L264,463 L0,463 Z" fill="var(--red)"/>
      <path d="M0,275 C55,222 190,218 264,272 L264,463 L0,463 Z" fill="var(--teal)" stroke="var(--white)" stroke-width="2.5"/>
    </svg>
    <p class="brand-name">HARBOR SHELTER ALLIANCE</p>
    <div class="contact">
      <h1 class="contact__name">DANIEL REYES</h1>
      <p class="contact__title">CEO/FOUNDER</p>
      <address class="contact__address">
        Harbor shelter alliance<br>
        1420 Willow Bend Road<br>
        Fairview, Oregon 97024
      </address>
      <ul class="contact__list">
        <li>
          <svg class="contact__icon" viewBox="0 0 10 10" aria-hidden="true"><path d="M2,0.5 L4,2.8 L3,4 C3.8,5.6 4.6,6.4 6,7 L7.2,6 L9.5,8 L8.2,9.5 C4,9 1,6 0.5,1.8 Z" fill="var(--yellow)"/></svg>
          555 210 4836
        </li>
        <li>
          <svg class="contact__icon" viewBox="0 0 10 10" aria-hidden="true"><rect x="0" y="2" width="10" height="6.5" fill="var(--yellow)"/><path d="M0,2 L5,5.8 L10,2" fill="none" stroke="var(--teal)" stroke-width="1"/></svg>
          daniel@harborshelter.org
        </li>
        <li>
          <svg class="contact__icon" viewBox="0 0 10 10" aria-hidden="true"><circle cx="5" cy="5" r="4.8" fill="var(--yellow)"/><path d="M0.5,5 H9.5 M5,0.5 C3,3 3,7 5,9.5 M5,0.5 C7,3 7,7 5,9.5" fill="none" stroke="var(--teal)" stroke-width="0.8"/></svg>
          www.harborshelter.org
        </li>
      </ul>
    </div>
  </section>

  <section class="card card--back" aria-label="Business card back">
    <p class="brand-name">HARBOR SHELTER ALLIANCE</p>
    <p class="tagline">Opening every door to home</p>
  </section>
</main>
</body>
</html>
```